Need Help having my business card stand out

I am the owner of Birchway Canine Training and would like for my business cards to stand out. I have been trying to keep designing them myself but I can't get what I have in my head on the card. I will try my best to post templates that I like for inspirations. I want something unique but elegant. I don't want in to look cartoony or cheesy. It needs to pop in a pet shop but also in a coffee shop or gym.

Target Market(s)

Dog owners, Married ,No young kids Jr High school kids and up (maybe kids on the way) Executives, Stay at home moms/wives, Small business owners

Industry/Entity Type

Dog Training

Contact Information for Business Card

Lowell Spratt, 281-904-3376, info@birchwaycanine.example, www.birchwaycanine.example

Colors

Designer to choose colors to be used in the design.

Requirements
Must have
• my logo
Should not have
• Cursive lettering

```html
<!DOCTYPE html>
<html lang="en">
<head>
<meta charset="utf-8">
<title>Birchway Canine Training – Business Card</title>
<link rel="stylesheet" href="https://fonts.googleapis.com/css2?family=Open+Sans:wght@300;400;600;700;800&display=swap">
<style>
  :root {
    --backdrop: #4a8fdc;
    --card-white: #ffffff;
    --navy: #0f2147;
    --ink-grey: #5d6573;
    --accent-blue: #3b8fe6;
    --back-top: #2a80d6;
    --back-bottom: #0c3a74;
    --on-dark: #ffffff;
  }
  * { box-sizing: border-box; margin: 0; padding: 0; }
  html, body {
    width: 1200px; height: 914px; overflow: hidden;
    background: var(--backdrop);
    font-family: "Open Sans", sans-serif;
  }
  .sheet {
    position: relative; width: 1200px; height: 914px;
    display: flex; justify-content: center; align-items: center; gap: 60px;
  }
  .card {
    position: relative; width: 340px; height: 595px;
    box-shadow: 0 18px 40px rgba(10, 40, 90, 0.35);
    overflow: hidden;
  }
  .notch {
    position: absolute; left: 50%; width: 26px; height: 12px;
    transform: translateX(-50%);
  }

  /* Front */
  .card-front { background: var(--card-white); color: var(--navy); }
  .card-front .notch { top: 0; background: var(--accent-blue); clip-path: polygon(0 0, 100% 0, 50% 100%); }
  .front-brand {
    position: absolute; top: 78px; left: 0; right: 0; text-align: center;
    font-weight: 800; font-size: 25px; line-height: 1.15; color: var(--navy);
  }
  .front-person { position: absolute; top: 210px; left: 40px; }
  .person-name { font-size: 25px; color: var(--navy); }
  .person-name .first { font-weight: 700; }
  .person-name .last { font-weight: 300; }
  .person-role {
    font-size: 12px; letter-spacing: 1px; color: var(--accent-blue);
    font-weight: 400; margin-top: 2px;
  }
  .contact-list {
    position: absolute; top: 330px; left: 40px; right: 30px;
    list-style: none; font-size: 12.5px; color: var(--ink-grey);
  }
  .contact-list li { display: flex; gap: 10px; margin-bottom: 12px; line-height: 1.45; }
  .contact-list svg { flex: 0 0 14px; width: 14px; height: 14px; margin-top: 2px; fill: var(--navy); }

  /* Back */
  .card-back {
    background: linear-gradient(180deg, var(--back-top) 0%, var(--back-bottom) 100%);
    color: var(--on-dark);
  }
  .card-back .notch { bottom: 0; background: var(--back-top); clip-path: polygon(50% 0, 100% 100%, 0 100%); }
  .back-tagline {
    position: absolute; top: 150px; left: 0; right: 0; text-align: center;
    font-size: 12px; letter-spacing: 3px; font-weight: 600;
  }
  .back-brand {
    position: absolute; top: 205px; left: 50px; right: 50px; text-align: center;
    font-size: 30px; font-weight: 800; line-height: 1.15;
  }
  .back-rule {
    position: absolute; top: 300px; height: 2px; width: 40px; background: var(--on-dark);
  }
  .back-rule.left { left: 0; }
  .back-rule.right { right: 0; }
  .back-web {
    position: absolute; bottom: 62px; left: 0; right: 0; text-align: center;
    font-size: 15px; font-weight: 700; letter-spacing: 0.3px;
  }
</style>
</head>
<body>
<main class="sheet">
  <section class="card card-front" aria-label="Business card front">
    <span class="notch"></span>
    <div class="front-brand">Birchway Canine<br>Training</div>
    <div class="front-person">
      <div class="person-name"><span class="first">Lowell</span> <span class="last">Spratt</span></div>
      <div class="person-role">FOUNDER</div>
    </div>
    <ul class="contact-list">
      <li>
        <svg viewBox="0 0 24 24" aria-hidden="true"><path d="M12 2a7 7 0 0 0-7 7c0 5 7 13 7 13s7-8 7-13a7 7 0 0 0-7-7zm0 9.5A2.5 2.5 0 1 1 12 6.5a2.5 2.5 0 0 1 0 5z"/></svg>
        <span>000 Harlow Ave., Suite 300,<br>Fenwick, US 0000</span>
      </li>
      <li>
        <svg viewBox="0 0 24 24" aria-hidden="true"><path d="M6.6 10.8a15 15 0 0 0 6.6 6.6l2.2-2.2a1 1 0 0 1 1-.25 11 11 0 0 0 3.6.6 1 1 0 0 1 1 1V20a1 1 0 0 1-1 1A17 17 0 0 1 3 4a1 1 0 0 1 1-1h3.5a1 1 0 0 1 1 1 11 11 0 0 0 .6 3.6 1 1 0 0 1-.25 1z"/></svg>
        <span>281-904-3376</span>
      </li>
      <li>
        <svg viewBox="0 0 24 24" aria-hidden="true"><path d="M3 5h18a1 1 0 0 1 1 1v12a1 1 0 0 1-1 1H3a1 1 0 0 1-1-1V6a1 1 0 0 1 1-1zm9 7 8-5H4z"/></svg>
        <span>info@birchwaycanine.example</span>
      </li>
      <li>
        <svg viewBox="0 0 24 24" aria-hidden="true"><path d="M12 2a10 10 0 1 0 0 20 10 10 0 0 0 0-20zm6.9 9h-3a15 15 0 0 0-1.3-5.6A8 8 0 0 1 18.9 11zM12 4c.9 1.2 1.7 3.6 1.9 7h-3.8c.2-3.4 1-5.8 1.9-7zM9.4 5.4A15 15 0 0 0 8.1 11h-3a8 8 0 0 1 4.3-5.6zM5.1 13h3a15 15 0 0 0 1.3 5.6A8 8 0 0 1 5.1 13zM12 20c-.9-1.2-1.7-3.6-1.9-7h3.8c-.2 3.4-1 5.8-1.9 7zm2.6-1.4a15 15 0 0 0 1.3-5.6h3a8 8 0 0 1-4.3 5.6z"/></svg>
        <span>www.birchwaycanine.example</span>
      </li>
    </ul>
  </section>

  <section class="card card-back" aria-label="Business card back">
    <div class="back-tagline">YOUR DOG TRAINER FOR LIFE</div>
    <div class="back-brand">Birchway Canine Training</div>
    <span class="back-rule left"></span>
    <span class="back-rule right"></span>
    <div class="back-web">www.birchwaycanine.example</div>
    <span class="notch"></span>
  </section>
</main>
</body>
</html>
```